Corvane Capital Business Cards

These are professional business cards that are for my family office.
Put fake emails and phone numbers as of now until I finalize those components. This family office controls my families investments, assets, and future. The cards should be professional.
..
.
.
.
I just uploaded another variation of a logo I would like to see as a business card to I am inbeteen which logo to use

Target Market(s)

business

Industry/Entity Type

business

Contact Information for Business Card

Professional, wealth related, finance related.

Requirements
Must have
• Logo

```html
<!DOCTYPE html>
<html lang="en">
<head>
<meta charset="UTF-8">
<title>Corvane Capital Business Cards</title>
<link href="https://fonts.googleapis.com/css2?family=Cinzel:wght@600&family=Montserrat:wght@400;500;700&display=swap" rel="stylesheet">
<style>
  :root {
    --navy: #1c2130;
    --grey-band: #a9a9a9;
    --grey-faint: #d9d9dc;
    --paper: #ffffff;
    --stage: #e9e9eb;
    --ink: #1c2130;
    --ink-soft: #3a3f4c;
  }
  * { margin: 0; padding: 0; box-sizing: border-box; }
  html, body { width: 1200px; height: 875px; overflow: hidden; }
  body {
    background: var(--stage);
    display: flex;
    align-items: center;
    justify-content: center;
    gap: 40px;
    font-family: 'Montserrat', sans-serif;
  }
  .card {
    position: relative;
    width: 540px;
    height: 309px;
    background: var(--paper);
    border-radius: 18px;
    overflow: hidden;
    box-shadow: 0 10px 30px rgba(0,0,0,0.12);
  }
  .card-bands {
    position: absolute;
    left: 0; bottom: 0;
    width: 540px; height: 40px;
  }
  .band-navy { fill: var(--navy); }
  .band-grey { fill: var(--grey-band); }

  /* Front */
  .front-mark {
    position: absolute;
    left: 50%; top: 46%;
    transform: translate(-50%, -50%);
    width: 260px; height: 260px;
  }
  .front-mark circle { fill: none; stroke: var(--grey-faint); stroke-width: 8; }
  .front-name {
    position: absolute;
    left: 0; right: 0; top: 46%;
    transform: translateY(-50%);
    text-align: center;
    font-family: 'Cinzel', serif;
    font-weight: 600;
    font-size: 44px;
    letter-spacing: 1px;
    color: var(--navy);
  }

  /* Back */
  .brand-block {
    position: absolute;
    left: 30px; top: 64px;
    width: 230px;
    display: flex;
    flex-direction: column;
    align-items: center;
    gap: 14px;
  }
  .brand-circle {
    width: 96px; height: 96px;
    border: 3px solid var(--navy);
    border-radius: 50%;
  }
  .brand-name {
    font-family: 'Cinzel', serif;
    font-weight: 600;
    font-size: 22px;
    color: var(--navy);
    letter-spacing: 0.5px;
  }
  .divider {
    position: absolute;
    left: 284px; top: 70px;
    width: 1.5px; height: 150px;
    background: var(--navy);
  }
  .contact {
    position: absolute;
    left: 304px; top: 62px;
    color: var(--ink-soft);
  }
  .contact-name {
    font-weight: 700;
    font-size: 19px;
    color: var(--ink);
  }
  .contact-role {
    font-size: 10.5px;
    margin-top: 1px;
    margin-left: 12px;
  }
  .contact-address {
    font-size: 11px;
    line-height: 1.3;
    margin-top: 12px;
    margin-left: 24px;
  }
  .contact-list {
    list-style: none;
    margin-top: 12px;
    margin-left: 24px;
    font-size: 11px;
  }
  .contact-list li {
    display: flex;
    align-items: center;
    gap: 8px;
    line-height: 1.75;
  }
  .contact-list svg { width: 11px; height: 11px; fill: var(--navy); flex: none; }
</style>
</head>
<body>

  <section class="card card-front" aria-label="Card front">
    <svg class="front-mark" viewBox="0 0 260 260" aria-hidden="true"><circle cx="130" cy="130" r="122"/></svg>
    <div class="front-name">Corvane Capital</div>
    <svg class="card-bands" viewBox="0 0 540 40" aria-hidden="true">
      <polygon class="band-navy" points="0,30 330,30 320,40 0,40"/>
      <polygon class="band-grey" points="342,14 540,14 540,40 324,40"/>
    </svg>
  </section>

  <section class="card card-back" aria-label="Card back">
    <div class="brand-block">
      <div class="brand-circle"></div>
      <div class="brand-name">Corvane Capital</div>
    </div>
    <div class="divider"></div>
    <div class="contact">
      <div class="contact-name">Marcus Ellery</div>
      <div class="contact-role">Owner</div>
      <div class="contact-address">42 Harbor View Court<br>Lindale, NJ 07811 USA</div>
      <ul class="contact-list">
        <li><svg viewBox="0 0 24 24"><path d="M6.6 10.8a15.1 15.1 0 0 0 6.6 6.6l2.2-2.2a1 1 0 0 1 1-.25 11.4 11.4 0 0 0 3.6.57 1 1 0 0 1 1 1V20a1 1 0 0 1-1 1A17 17 0 0 1 3 4a1 1 0 0 1 1-1h3.5a1 1 0 0 1 1 1 11.4 11.4 0 0 0 .57 3.6 1 1 0 0 1-.25 1z"/></svg>(555)214-7730</li>
        <li><svg viewBox="0 0 24 24"><path d="M2 5h20v14H2z M2 5l10 8 10-8" /></svg>hello@corvanecapital.com</li>
        <li><svg viewBox="0 0 24 24"><circle cx="12" cy="12" r="10"/></svg>www.corvanecapital.com</li>
      </ul>
    </div>
    <svg class="card-bands" viewBox="0 0 540 40" aria-hidden="true">
      <polygon class="band-navy" points="0,30 345,30 335,40 0,40"/>
      <polygon class="band-grey" points="358,12 540,12 540,40 338,40"/>
    </svg>
  </section>

</body>
</html>
```